One of a kind, 100% Pure & Natural Skincare line needs stunning product label

We need product label design for new natural skincare company called Tolven & Mira Skincare. We create luxurious, 100% pure & natural skincare that is free from ingredients that may be potentially irritating to the skin. No toxins, preservatives or additives. Our initial product is Harbor Face Balm, a nourishing face cream that suits discerning women with mature skin and those with dry/sensitive skin needing extra hydration. Also those that choose to minimize their exposure to environmental toxins. Our brand is simple yet elegant, supporting a holistic, authentic lifestyle and embracing natural skincare.

Target Market(s)

Discerning women with mature skin and those with dry/sensitive skin needing extra hydration. Also those that choose to minimize their exposure to environmental toxins.

Industry/Entity Type

Skin Care Product

Font styles to use
Sans Serif
Script

Colors
f9d9e8
fef1ee

Requirements
Must have
• The Logo.
HARBOR FACE BALM
EMBRACING NATURAL SKINCARE
Labels must be feminine, simple/minimal yet stylish. Uncluttered yet elegant.
This is a very natural product with minimal ingredients.
Nice to have
• The logo can be incorporated in to the label, or It can be left separate as a sticker on top of the jar. The product is a firm balm consistency and is in frosted glass jars with matt silver lids.
Jar height is 45mm, width is 60mm.
Label height: 28mm and length 185mm
Should not have
• Natural or farmers market type theme. No Bold/loud lettering.

```html
<!DOCTYPE html>
<html lang="en">
<head>
<meta charset="utf-8">
<title>Tolven &amp; Mira Skincare – Harbor Face Balm Label</title>
<link href="https://fonts.googleapis.com/css2?family=Montserrat:wght@300;400;600&display=swap" rel="stylesheet">
<style>
  :root {
    --blush-ring: #fcefec;
    --blush-fill: #fcf2f0;
    --rose-deep: #f4b6c6;
    --rose-soft: #f9d9e8;
    --ink: #1c1c1c;
    --grey-mark: #a9a9a9;
    --frame-grey: #c4c4c4;
    --bleed-blue: #bfe0ef;
    --white: #ffffff;
  }
  * { box-sizing: border-box; margin: 0; padding: 0; }
  html, body { width: 1200px; height: 1000px; overflow: hidden; background: var(--white); }
  body { position: relative; font-family: "Montserrat", Arial, sans-serif; color: var(--ink); }

  /* Lid sticker */
  .lid-sticker { position: absolute; left: 338px; top: 93px; width: 524px; height: 524px; border-radius: 50%; border: 7px solid var(--blush-ring); }
  .lid-sticker__face { position: absolute; left: 22px; top: 22px; width: 466px; height: 466px; border-radius: 50%; background: var(--blush-fill); }
  .brand-lockup { position: absolute; left: 0; right: 0; top: 200px; display: flex; align-items: center; justify-content: center; gap: 12px; }
  .brand-lockup__dot { width: 14px; height: 14px; border-radius: 50%; background: var(--rose-deep); }
  .brand-lockup__name { font-weight: 300; font-size: 30px; letter-spacing: 1px; color: var(--ink); }

  /* Wrap label */
  .label-bleed { position: absolute; left: 33px; top: 748px; width: 1134px; height: 203px; border: 1px dashed var(--bleed-blue); }
  .label-trim { position: absolute; left: 52px; top: 767px; width: 1097px; height: 166px; border: 1px solid var(--frame-grey); }
  .label-safe { position: absolute; left: 71px; top: 786px; width: 1059px; height: 128px; border: 1px dashed var(--bleed-blue); }

  .label-panel { position: absolute; font-size: 10.5px; line-height: 13px; }
  .label-panel b { font-weight: 600; }
  .label-panel p { margin-bottom: 14px; }
  .panel-info { left: 77px; top: 792px; width: 320px; }
  .panel-care { left: 806px; top: 790px; width: 300px; }
  .panel-care p { margin-bottom: 9px; }

  .front-band { position: absolute; left: 402px; top: 768px; width: 398px; height: 165px; background: linear-gradient(90deg, var(--rose-deep) 0%, var(--rose-soft) 45%, var(--white) 100%); overflow: hidden; }
  .front-band__motif { position: absolute; left: 18px; top: 24px; width: 150px; height: 140px; border-radius: 60% 40% 0 0; background: rgba(255,255,255,0.25); }
  .front-band__sprig { position: absolute; left: 180px; top: 20px; width: 36px; height: 46px; border-radius: 50% 50% 8px 8px; background: rgba(28,28,28,0.75); }
  .front-band__title { position: absolute; left: 0; right: 0; top: 68px; text-align: center; font-weight: 300; font-size: 21px; letter-spacing: 0.5px; }
  .front-band__rule { position: absolute; left: 124px; width: 150px; top: 93px; height: 1px; background: var(--ink); }
  .front-band__tagline { position: absolute; left: 0; right: 0; top: 97px; text-align: center; font-size: 8.5px; letter-spacing: 0.8px; }
  .front-band__weight { position: absolute; left: 0; right: 0; top: 129px; text-align: center; font-size: 6px; }

  .leaf-accent { position: absolute; width: 40px; height: 38px; border-radius: 50%; background: #d0d0d0; opacity: 0.6; }
  .leaf-accent--left { left: 72px; top: 853px; width: 32px; height: 28px; }
  .leaf-accent--right { left: 1080px; top: 836px; }

  .contact { display: flex; align-items: center; gap: 5px; }
  .pao-icon { position: absolute; left: 1094px; top: 886px; }
</style>
</head>
<body>

  <section class="lid-sticker" aria-label="Lid sticker">
    <div class="lid-sticker__face">
      <div class="brand-lockup">
        <span class="brand-lockup__dot"></span>
        <span class="brand-lockup__name">Tolven &amp; Mira Skincare</span>
      </div>
    </div>
  </section>

  <div class="label-bleed"></div>
  <div class="label-trim"></div>
  <div class="label-safe"></div>

  <div class="label-panel panel-info">
    <p><b>INGREDIENTS :</b>&nbsp; Tallow from pasture raised goats, frankincense, sandalwood &amp; myrrh essential oils.</p>
    <p><b>DIRECTIONS :</b>&nbsp; Soften small amount in palm of<br>hand &amp; gently massage into skin as often as</p>
    <p>Allergy patch test recommended. If irritation occurs, discontinue use.</p>
  </div>
  <div class="leaf-accent leaf-accent--left" role="img" aria-label="Faint leaf sprig ornament"></div>

  <section class="front-band" aria-label="Front panel">
    <div class="front-band__motif" role="img" aria-label="Soft pale leaf and flower ornament"></div>
    <div class="front-band__sprig" role="img" aria-label="Small dark leaf sprig ornament"></div>
    <h1 class="front-band__title">HARBOR FACE BALM</h1>
    <div class="front-band__rule"></div>
    <p class="front-band__tagline">EMBRACING NATURAL SKINCARE</p>
    <p class="front-band__weight">NET WT 1.76 oz</p>
  </section>

  <div class="label-panel panel-care">
    <p><b>CAUTION:</b>&nbsp; Keep out of reach of children. If pregnant or breastfeeding, consult your healthcare practitioner. Avoid contact with eyes &amp; sensitive areas.</p>
    <p>Store below 25°C</p>
    <p>MADE IN AUSTRALIA</p>
    <p>B#</p>
    <p class="contact">
      <svg width="13" height="9" viewBox="0 0 13 9" aria-hidden="true"><rect x="0.5" y="0.5" width="12" height="8" fill="none" stroke="#1c1c1c"/><path d="M0.5 0.5 L6.5 5 L12.5 0.5" fill="none" stroke="#1c1c1c"/></svg>
      info@tolvenandmiraskincare.com.au
    </p>
  </div>
  <div class="leaf-accent leaf-accent--right" role="img" aria-label="Faint leaf sprig ornament"></div>

  <svg class="pao-icon" width="24" height="24" viewBox="0 0 24 24" role="img" aria-label="Period after opening 6 months">
    <path d="M3 6 L20 2" stroke="#1c1c1c" stroke-width="1.5" fill="none"/>
    <rect x="3" y="9" width="18" height="13" rx="1.5" fill="none" stroke="#1c1c1c" stroke-width="1.5"/>
    <text x="12" y="19" text-anchor="middle" font-family="Montserrat, Arial, sans-serif" font-size="6.5" font-weight="600">6M</text>
  </svg>

</body>
</html>
```